Zing Webcomic

A simple signup landing page and blog design for an upcoming webcomic. I am mostly looking for a flat UI with a simple color scheme. I want to showcase a large background image and the comic title image. I have all the technicals figured out (I am a web developer by trade), so all I need now is a solid design I like.

The signup for should only have one field (email) and have text above it, and smaller text below it.

The blog, I am thinking, should be in the style of comic book pages. The home page would be blocks with large white outlines, with the article pages being an extension of that. As I stated before, should be fairly minimalist, but fun. Also, no sidebar or ads, IE single column. I have attached a simple mockup/layout of the blog to give a general idea of what I am going for.

I have attached the Logo and Background art (uncolored) for reference. Don't worry about the background image blending in, I can take care of that when the design is implemented. I will be focusing on layout and overall look, not necessarily readability (which I can fix).

~Please DO NOT take these examples literally. I will describe what I like about each example.~

Signup pages:
http://example-plaza.test/landing-page-type-photo/
http://www.lanternhop.test/showcase/website-design/814/10-most-beautiful-landing-pages-in-minimalist-style
http://quillnest.test/47-modern-landing-pages-showcasing-inspirational-web-design/
Great examples of minimalist design. However, instead of text or other content, there should be a simple signup form, as described above. Also think a lot more "playful" rather than super professional.

Blog:
http://vrakk.test/
Awesome example of a single column, minimal design. Needs to be more "comicbook style" though.
http://tidyrows.test/
Another good example of minimal design blog.
http://makerbarn.test/wp-content/uploads/res-blogs-5.jpg
I like the timeline feel here. Combine that with a comic book page kind of thing, and I think you have a winner.

Actual webcomic landing (not required):
http://www.lunarfoxpanels.test/comic.php?date=20021104#.U90ysYBdUvU
I like the navigation. It makes the atmosphere nice for the comic. The page layout itself is WAY too busy.
http://www.dime-galaxy.test/comic/
Fairly common webcomic, but their navigation and page layout is nice.
http://qvmp.test/936/
Another common webcomic. The simple page layout makes it easy for people to get started I think.

So there you have it. I will try my best to keep updating and adding to the description. If you have any questions, please don't hesitate to ask.
Updates

Hey Guys, I am really appreciating all the effort you have been putting in. I am amazed to see all the awesome designs and all the care taken with the project. I am just writing everyone to let you know that I have uploaded a simple layout/wireframe of the blog, to give an idea of what I am going for. Can't wait to see how things progress, and good luck to everyone!

Industry/Entity Type

Trade

Font styles to use
Sans Serif

Requirements
Must have
• Must showcase a large background image (does not have to cover the entire background). Should be a flat UI as well. Should be mostly neutral with splashes of blue or purple. Social links should also be somewhere (twitter, facebook, etc.).
Nice to have
• I am thinking something with rounded boxes, but I can live without them. A more "fun" design as opposed to more professional is definitely nice to have.

If you would like to try a stab at the actual comic page display and navigation, you are welcome to submit something. It should not be a main priority though.

Being responsive is not a requirement, but it would be nice to have.
Should not have
• A billion links in the navigation or look too busy.
No sidebar or advertisements. Should be a clean design.

```html
<!DOCTYPE html>
<html lang="en">
<head>
<meta charset="utf-8">
<title>Zing Webcomic – Sign up</title>
<link href="https://fonts.googleapis.com/css2?family=Kaushan+Script&family=Source+Sans+3:wght@400;600;700&display=swap" rel="stylesheet">
<style>
  :root {
    --bg-dark: #1c1c1c;
    --bg-mid: #2e2e2e;
    --card: #ffffff;
    --purple: #663399;
    --purple-deep: #5a2a8c;
    --ink: #333333;
    --muted: #555555;
    --field-border: #8a8a8a;
    --placeholder: #9a9a9a;
    --green: #7bbf1e;
    --green-dark: #4f8a10;
    --white: #ffffff;
  }
  * { box-sizing: border-box; margin: 0; padding: 0; }
  html, body { width: 1200px; height: 676px; overflow: hidden; }
  body {
    position: relative;
    background: var(--bg-dark);
    font-family: "Source Sans 3", sans-serif;
    color: var(--ink);
  }
  .hero-art {
    position: absolute; inset: 0;
    background: radial-gradient(ellipse at 50% 40%, var(--bg-mid) 0%, #242424 55%, var(--bg-dark) 100%);
  }
  .signup-card {
    position: absolute;
    left: 310px; top: 90px;
    width: 580px; height: 468px;
    background: var(--card);
    border-radius: 12px 18px 10px 16px;
    text-align: center;
  }
  .brand {
    position: absolute;
    left: 50%; top: 38px;
    transform: translateX(-50%);
    display: flex; align-items: center; gap: 10px;
    background: var(--card);
    padding: 10px 22px;
    border-radius: 14px;
  }
  .brand-dot { width: 16px; height: 16px; border-radius: 50%; background: var(--purple); }
  .brand-name {
    font-family: "Source Sans 3", sans-serif;
    font-weight: 700; font-size: 40px; line-height: 1;
    color: var(--purple); letter-spacing: 2px;
  }
  .signup-title {
    position: absolute; left: 0; right: 0; top: 52px;
    font-family: "Kaushan Script", cursive;
    font-weight: 400; font-size: 34px; line-height: 42px;
    color: var(--purple);
  }
  .signup-tagline {
    position: absolute; right: 88px; top: 98px;
    font-size: 11.5px; line-height: 14px; color: var(--ink);
    white-space: nowrap;
  }
  .signup-pitch {
    position: absolute; left: 0; right: 0; top: 142px;
    font-size: 14.5px; font-weight: 600; letter-spacing: 0.3px;
    line-height: 22px; text-transform: uppercase; color: var(--ink);
  }
  .signup-form {
    position: absolute; left: 130px; top: 204px; width: 320px;
  }
  .email-field {
    width: 320px; height: 42px;
    border: 1px solid var(--field-border); border-radius: 2px;
    font-family: inherit; font-size: 13px; text-align: center;
    color: var(--ink);
  }
  .email-field::placeholder { color: var(--placeholder); }
  .signup-button {
    margin-top: 24px;
    width: 320px; height: 42px;
    background: var(--purple); color: var(--white);
    border: none; border-bottom: 2px solid var(--purple-deep);
    font-family: inherit; font-weight: 700; font-size: 15px;
    text-transform: uppercase;
  }
  .signup-note {
    position: absolute; left: 118px; width: 344px; top: 332px;
    font-size: 12.5px; line-height: 19px; color: var(--muted);
  }
  .blog-link {
    position: absolute; left: 840px; top: 480px;
    width: 110px; height: 86px;
  }
  .social-links {
    position: absolute; top: 596px; left: 0; right: 0;
    display: flex; justify-content: center; gap: 8px;
    list-style: none;
  }
  .social-links li { width: 26px; height: 26px; border-radius: 50%; background: var(--white); }
  .social-links li.is-active { background: var(--green); }
  .visually-hidden { position: absolute; width: 1px; height: 1px; overflow: hidden; clip: rect(0 0 0 0); }
  .site-footer {
    position: absolute; top: 633px; left: 0; right: 0;
    text-align: center; font-size: 11px; color: var(--white);
  }
</style>
</head>
<body>
  <div class="hero-art" role="img" aria-label="Uncoloured comic art of armed heroes in front of a city skyline"></div>

  <main class="signup-card">
    <h1 class="signup-title">Sign up For a Zing webcomic</h1>
    <p class="signup-tagline">Get free comics like Comet Raiders, Void Protocol, Ashboy and more!</p>
    <p class="signup-pitch">Start amassing a Zing webcomic and be<br>the envy of your friends and foes alike!</p>
    <form class="signup-form">
      <input class="email-field" type="email" placeholder="Enter your email" aria-label="Email address">
      <button class="signup-button" type="submit">Sign up</button>
    </form>
    <p class="signup-note">Lorem ipsum dolor sit amet, consectetur adipisicing elit, sed do eius mod tempor incididunt ut labore et dolore magna aliqua. Ut enim ad minim veniam, quis nostrud exercitation ullamco laboris nisi ut aliquip ex ea commodo consequat.</p>
  </main>

  <div class="brand">
    <span class="brand-dot"></span>
    <span class="brand-name">ZING</span>
  </div>

  <a class="blog-link" href="#" aria-label="Our blog">
    <svg width="110" height="86" viewBox="0 0 110 86">
      <path d="M4 22 H58 V4 L106 43 L58 82 V64 H4 Z" fill="var(--white)"/>
      <path d="M10 28 H64 V16 L96 43 L64 70 V58 H10 Z" fill="var(--green)" stroke="var(--green-dark)" stroke-width="2"/>
      <text x="40" y="40" text-anchor="middle" font-family="Source Sans 3, sans-serif" font-weight="700" font-size="10" fill="var(--white)">OUR</text>
      <text x="42" y="54" text-anchor="middle" font-family="Source Sans 3, sans-serif" font-weight="700" font-size="13" fill="var(--white)">BLOG</text>
    </svg>
  </a>

  <ul class="social-links">
    <li><span class="visually-hidden">Social link 1</span></li>
    <li><span class="visually-hidden">Social link 2</span></li>
    <li class="is-active"><span class="visually-hidden">Social link 3</span></li>
    <li><span class="visually-hidden">Social link 4</span></li>
    <li><span class="visually-hidden">Social link 5</span></li>
    <li><span class="visually-hidden">Social link 6</span></li>
  </ul>

  <footer class="site-footer">Copyright © 2014 Zing Webcomic All rights reserved.</footer>
</body>
</html>
```